Website redesign for job agency recruitment

Please refer to the attached document, “Tarvenly Work Website Brief,” for comprehensive details regarding the scope, objectives, and requirements of this website redesign project.

For imagery you can use images from this website https://www.pixelmarrowfoto.com or any other you regularly use.

Target Market(s)

Jobseekers and Companies looking for general labour

Industry/Entity Type

Services: Oil, Gas and Mining, Administrative, Construction and Trades, Warehouse and Logistics and, Manufacturing.

Number of Pages Required

5+ page

Font styles to use
Serif
Other font styles liked:
• Inter, Open-Sans or similar.

Requirements
Must have
• The requirements highlighted in the Word document attached. The final design needs to be provided in Figma including all viewports (Desktop, mobiel and tablet)
Should not have
• Website we like as a reference: www.brevicktalentco.com, www.qelvaworks.com, www.zunmarra.com, www.ferrowhires.com, www.9vtalentpool.com, www.hiringwithtrello.ca

```html
<!DOCTYPE html>
<html lang="en">
<head>
<meta charset="utf-8">
<title>Tarvenly Work Agency</title>
<link rel="stylesheet" href="https://fonts.googleapis.com/css2?family=Prata&family=Outfit:wght@400;500&display=swap">
<style>
:root{
  --navy:#0f3485;
  --gold:#f0bf1a;
  --ink:#1f1f1f;
  --muted:#3a3a3a;
  --soft:#f4f2f3;
  --dark:#262626;
  --line:#d9d9e2;
  --white:#ffffff;
}
*{box-sizing:border-box;margin:0;padding:0}
html,body{width:1200px;height:2201px;overflow:hidden;background:var(--white)}
body{position:relative;font-family:"Outfit",sans-serif;color:var(--ink)}
.abs{position:absolute}
/* header */
.brand{left:111px;top:30px;display:flex;align-items:center;gap:10px}
.brand-dot{width:46px;height:46px;border-radius:50%;background:var(--navy)}
.brand-name{font-size:15px;font-weight:500;color:var(--navy);line-height:1.2;width:120px}
.contact{top:18px;display:flex;gap:12px;align-items:flex-start}
.contact svg{margin-top:10px}
.contact-label{font-size:12px;letter-spacing:.3px;color:var(--ink)}
.contact-num{font-size:14px;color:var(--navy);margin-top:6px}
.nav{top:77px;right:114px;display:flex;gap:32px;font-size:14px;letter-spacing:.3px}
.nav a{color:var(--ink);text-decoration:none}
.nav a.active{color:var(--gold)}
/* hero */
.hero{left:0;top:112px;width:1200px;height:488px;overflow:hidden;
  border-top-right-radius:200px 150px;border-bottom-left-radius:170px 150px;
  background:
   linear-gradient(90deg,rgba(20,40,80,.85) 0%,rgba(40,60,100,.55) 28%,rgba(0,0,0,0) 34%),
   linear-gradient(180deg,#b9c8dc 0%,#d9d3c8 35%,#e7a458 65%,#b86a2a 100%)}
.hero-title{left:0;width:1200px;top:156px;text-align:center;font-family:"Prata",serif;font-size:38px;font-weight:400;line-height:57px;color:#161616}
.btn{display:inline-flex;align-items:center;justify-content:center;height:43px;border-radius:22px;font-size:15px;color:var(--white)}
.btn-navy{background:var(--navy)}
.btn-gold{background:var(--gold)}
/* services */
.section-title{font-family:"Prata",serif;font-size:35px;font-weight:400;color:var(--navy)}
.rule{height:2px;width:63px;background:var(--gold)}
.tab{left:125px;width:303px;height:64px;border:1px solid var(--line);border-radius:10px 44px 0 44px;
  display:flex;align-items:center;justify-content:space-between;padding:0 22px 0 33px;font-size:14.5px;line-height:24px;letter-spacing:.2px}
.tab.active{background:var(--navy);border-color:var(--navy);color:var(--white)}
.tab-icon{width:18px;height:18px;border-radius:50%;background:var(--navy);display:flex;align-items:center;justify-content:center;flex:none}
.tab.active .tab-icon{background:var(--gold)}
.photo{overflow:hidden}
.service-photo{left:545px;top:786px;width:526px;height:254px;border-top-right-radius:100px 60px;border-bottom-left-radius:100px 60px;
  background:linear-gradient(180deg,#4a4b55 0%,#a56a3a 45%,#e08a2c 75%,#5a3620 100%)}
.service-head{left:564px;top:1082px;font-size:20px;font-weight:500;color:var(--navy)}
.service-copy{left:565px;top:1124px;width:524px;font-size:15px;line-height:29px;text-align:justify;color:var(--muted)}
/* footer backdrop sits under the about panel */
.footer-bg{left:0;top:1700px;width:1200px;height:501px;background:var(--dark)}
/* about */
.about{left:0;top:1346px;width:1200px;height:488px;background:var(--soft);
  border-top-right-radius:200px 150px;border-bottom-left-radius:190px 150px}
.about-copy{left:111px;top:1484px;width:479px;font-size:15px;line-height:29px;text-align:justify;color:var(--ink)}
.about-copy p+p{margin-top:12px}
.about-photo{left:661px;top:1417px;width:428px;height:347px;border-top-left-radius:150px 80px;border-bottom-right-radius:150px 100px;
  background:linear-gradient(160deg,#3b4656 0%,#566273 40%,#7a5a44 75%,#34302c 100%)}
/* footer */
.footer-brand{left:0;width:1200px;top:1900px;display:flex;flex-direction:column;align-items:center;gap:14px}
.footer-brand .brand-dot{width:56px;height:56px;background:var(--gold)}
.footer-name{font-size:16px;font-weight:500;color:var(--white)}
.footer-nav{left:0;width:1200px;top:2069px;text-align:center;font-size:14px;color:var(--white);letter-spacing:.2px;word-spacing:1px}
.footer-nav span{margin:0 17px}
.copyright{left:0;width:1200px;top:2121px;text-align:center;font-size:13.5px;color:var(--white);letter-spacing:.2px}
</style>
</head>
<body>

<div class="footer-bg abs"></div>

<header>
  <div class="brand abs"><span class="brand-dot"></span><span class="brand-name">Tarvenly Work Agency Ltd.</span></div>
  <div class="contact abs" style="left:727px">
    <svg width="20" height="18" viewBox="0 0 20 18" fill="none" stroke="#0f3485" stroke-width="1.4"><rect x="1" y="1" width="18" height="12" rx="2"/><path d="M5 13v4l4-4"/><path d="M5 5h10M5 9h7"/></svg>
    <div><div class="contact-label">TEXT</div><div class="contact-num">604-555-0147</div></div>
  </div>
  <div class="contact abs" style="left:951px">
    <svg width="18" height="18" viewBox="0 0 24 24" fill="none" stroke="#0f3485" stroke-width="1.6"><path d="M5 3h4l2 5-2.5 1.5a11 11 0 0 0 6 6L16 13l5 2v4a2 2 0 0 1-2 2A16 16 0 0 1 3 5a2 2 0 0 1 2-2z"/></svg>
    <div><div class="contact-label">TOLL-FREE</div><div class="contact-num">1-888-555-0193</div></div>
  </div>
  <nav class="nav abs">
    <a class="active" href="#">HOME</a><a href="#">CANDIDATES</a><a href="#">COMPANIES</a><a href="#">ABOUT US</a><a href="#">CONTACT</a><a href="#">FORMS &amp; LINKS</a>
  </nav>
</header>

<section>
  <div class="hero abs" role="img" aria-label="City skyline of glass towers at sunset"></div>
  <svg class="abs" style="left:0;top:112px" width="1200" height="488" viewBox="0 0 1200 488" fill="none">
    <path d="M1030 2 A170 125 0 0 1 1198 125" stroke="#0f3485" stroke-width="7"/>
    <path d="M2 338 A170 150 0 0 0 160 486" stroke="#f0bf1a" stroke-width="7"/>
  </svg>
  <h1 class="hero-title abs">CONNECTING TALENT WITH<br>OPPORTUNITY</h1>
  <a class="btn btn-navy abs" style="left:411px;top:286px;width:179px">FOR CANDIDATES</a>
  <a class="btn btn-gold abs" style="left:610px;top:286px;width:179px">FOR EMPLOYERS</a>
</section>

<section>
  <h2 class="section-title abs" style="left:0;width:1200px;text-align:center;top:676px">TWA SERVICES</h2>
  <div class="rule abs" style="left:568px;top:731px"></div>

  <div class="tab active abs" style="top:786px">OIL, GAS AND MINING<span class="tab-icon"><svg width="8" height="8" viewBox="0 0 8 8"><path d="M3 1l3 3-3 3" stroke="#0f3485" stroke-width="1.6" fill="none"/></svg></span></div>
  <div class="tab abs" style="top:883px">ADMINISTRATIVE<span class="tab-icon"><svg width="8" height="8" viewBox="0 0 8 8"><path d="M3 1l3 3-3 3" stroke="#fff" stroke-width="1.6" fill="none"/></svg></span></div>
  <div class="tab abs" style="top:979px">CONSTRUCTION AND<br>TRADES<span class="tab-icon"><svg width="8" height="8" viewBox="0 0 8 8"><path d="M3 1l3 3-3 3" stroke="#fff" stroke-width="1.6" fill="none"/></svg></span></div>
  <div class="tab abs" style="top:1076px">WAREHOUSE &amp; LOGISTICS<span class="tab-icon"><svg width="8" height="8" viewBox="0 0 8 8"><path d="M3 1l3 3-3 3" stroke="#fff" stroke-width="1.6" fill="none"/></svg></span></div>
  <div class="tab abs" style="top:1172px">MANUFACTURING<span class="tab-icon"><svg width="8" height="8" viewBox="0 0 8 8"><path d="M3 1l3 3-3 3" stroke="#fff" stroke-width="1.6" fill="none"/></svg></span></div>

  <div class="service-photo photo abs" role="img" aria-label="Oil pumpjack silhouetted against a sunset sky"></div>
  <svg class="abs" style="left:545px;top:786px" width="526" height="254" viewBox="0 0 526 254" fill="none">
    <path d="M420 2 A104 62 0 0 1 524 64" stroke="#0f3485" stroke-width="6"/>
    <path d="M2 190 A104 62 0 0 0 106 252" stroke="#f0bf1a" stroke-width="6"/>
  </svg>
  <h3 class="service-head abs">OIL, GAS AND MINING</h3>
  <p class="service-copy abs">Lorem ipsum dolor sit amet, consectetur adipiscing elit, sed do eiusmod tempor incididunt ut labore et dolore magna aliqua. Ut enim ad minim veniam, quis nostrud exercitation ullamco laboris nisi ut aliquip ex ea commodo consequat. Duis aute irure dolor in reprehenderit in voluptate velit esse cillum dolore eu fugiat nulla pariatur.</p>
</section>

<section>
  <div class="about abs"></div>
  <h2 class="section-title abs" style="left:111px;top:1398px">ABOUT TWA</h2>
  <div class="rule abs" style="left:111px;top:1456px"></div>
  <div class="about-copy abs">
    <p>Tarvenly Work Agency offers a complete range of staffing services to keep pace with your career or operational demands. We understand it's not only daunting but very costly in both time and money to make your business thrive in a rapidly changing environment.</p>
    <p>Our staffing and recruitment services are not just limited to finding good people. We are a Canada-wide team of capable search specialists, career counselors, HR specialists.</p>
  </div>
  <a class="btn btn-navy abs" style="left:111px;top:1728px;width:144px">LEARN MORE</a>

  <div class="about-photo photo abs" role="img" aria-label="Workers in hard hats grinding steel beams in a factory"></div>
  <svg class="abs" style="left:661px;top:1417px" width="428" height="347" viewBox="0 0 428 347" fill="none">
    <path d="M3 86 A150 82 0 0 1 150 3" stroke="#0f3485" stroke-width="6"/>
    <path d="M425 240 A150 104 0 0 1 280 344" stroke="#f0bf1a" stroke-width="6"/>
  </svg>
</section>

<footer>
  <div class="footer-brand abs"><span class="brand-dot"></span><span class="footer-name">Tarvenly Work Agency Ltd.</span></div>
  <div class="footer-nav abs">HOME<span>|</span>CANDIDATES<span>|</span>COMPANIES<span>|</span>ABOUT US<span>|</span>CONTACT<span>|</span>FORMS &amp; LINKS</div>
  <div class="copyright abs">© TARVENLY WORK AGENCY LTD. | ALL RIGHTS RESERVED 2026 | TERMS OF USE | LOGIN</div>
</footer>

</body>
</html>
```